Corvana Tongue Works, LLC

We need a business card that includes information about our business and conveys a reliable business that provides document translation services and interpreters for a variety of corporate and individual clients. We want to come across as professional, reliable, yet approachable. It should include the following on one side:

ESL / ENL Language Classes, Private Lessons, and Online Tutors
PLEXA Training and Testing
Translating & Interpreting Services
Contact us about Over-the-Phone Interpreting in over 200 languages
24/7/365
www.corvanatongue.example

The other side should include (555) 481-3062

Rhoda Pelling, President
482 Garnet Ave., Ste. 219
Indianapolis, IN 40917

Please add USA as part of the address. Also, please add rmpelling@corvanatongueworks.example as the e-mail address. Thank you.

Target Market(s)

Business professionals, their families, the international community

Industry/Entity Type

Business

Contact Information for Business Card

24/7/365
www.corvanatongue.example

(555) 481-3062

Rhoda Pelling, President
482 Garnet Ave., Ste. 219
Indianapolis, IN 40917
USA

Font styles to use
Sans Serif

Colors

Designer to choose colors to be used in the design.

Requirements
Must have
• See project description
• e-mail address and web address
• Phone number
Nice to have
• a globe
• physical address
Should not have
• Should not have the same color scheme as other agencies in our market in Indiana unless it is blue and black. No purple or yellow.

```html
<!DOCTYPE html>
<html lang="en">
<head>
<meta charset="utf-8">
<title>Corvana Tongue Works – Business Card</title>
<link rel="stylesheet" href="https://fonts.googleapis.com/css2?family=Roboto:wght@400;500&display=swap">
<style>
  :root {
    --bg: #e9e8e6;
    --card: #070707;
    --card-sheen: #1d1d1f;
    --blue: #2c9ad9;
    --white: #ffffff;
  }
  * { box-sizing: border-box; margin: 0; padding: 0; }
  html, body { width: 1200px; height: 930px; overflow: hidden; }
  body {
    background: var(--bg);
    font-family: "Roboto", Arial, sans-serif;
    position: relative;
  }
  .card {
    position: absolute;
    left: 250px;
    width: 700px;
    height: 400px;
    border-radius: 18px;
    overflow: hidden;
    background: linear-gradient(115deg, var(--card) 0%, var(--card) 45%, var(--card-sheen) 70%, var(--card) 100%);
    box-shadow: 0 10px 28px rgba(0,0,0,.25);
    color: var(--white);
  }
  .card--back { top: 40px; }
  .card--front { top: 490px; }

  .brand { position: absolute; display: flex; align-items: center; gap: 16px; }
  .brand__mark {
    width: 104px; height: 104px; border-radius: 50%;
    background: var(--blue); flex: none;
  }
  .brand__name { font-size: 34px; line-height: 1.02; font-weight: 400; color: var(--white); }
  .brand__name small { font-size: 15px; }

  .card--back .brand { left: 200px; top: 48px; }

  .services {
    position: absolute; left: 60px; right: 60px; top: 200px;
    text-align: center; font-size: 17px; line-height: 1.45; font-weight: 500;
  }
  .rule { position: absolute; height: 2px; background: var(--blue); }
  .card--back .rule--top { left: 120px; right: 120px; top: 186px; }
  .card--back .rule--bottom { left: 60px; right: 60px; top: 292px; }
  .contact-note {
    position: absolute; left: 40px; right: 40px; top: 306px;
    text-align: center; font-size: 17px; line-height: 1.45; font-weight: 500;
  }

  .wave { position: absolute; left: 0; top: 0; }
  .card--front .brand { left: 36px; top: 184px; }
  .card--front .brand__mark { width: 100px; height: 100px; }
  .card--front .brand__name { font-size: 30px; }
  .card--front .brand__name small { font-size: 14px; }
  .person { position: absolute; right: 70px; top: 158px; text-align: right; }
  .person__name { font-size: 30px; font-weight: 500; color: var(--blue); letter-spacing: .5px; }
  .person__title { font-size: 17px; color: var(--white); margin-top: 2px; }
  .person__bar { position: absolute; right: -22px; top: 2px; width: 4px; height: 58px; background: var(--white); }
  .person__accent { position: absolute; right: -40px; top: 2px; width: 12px; height: 58px; background: var(--blue); }
  .card--front .rule--name { left: 330px; right: 70px; top: 238px; }
  .address {
    position: absolute; right: 70px; top: 262px; text-align: right;
    font-size: 17px; line-height: 1.4;
  }
  .contacts {
    position: absolute; left: 150px; top: 300px; list-style: none;
    font-size: 17px; line-height: 1.55;
  }
  .contacts li { display: flex; align-items: center; gap: 10px; }
  .contacts svg { flex: none; }
</style>
</head>
<body>

<section class="card card--back" aria-label="Card back">
  <div class="brand">
    <span class="brand__mark"></span>
    <span class="brand__name">Corvana<br>Tongue<br>Works <small>LLC</small></span>
  </div>
  <div class="rule rule--top"></div>
  <p class="services">
    ESL / ENL Language Classes, Private Lessons, and Online Tutors<br>
    PLEXA Training and Testing<br>
    Translating &amp; Interpreting Services
  </p>
  <div class="rule rule--bottom"></div>
  <p class="contact-note">
    Contact us about Over-the-Phone Interpreting in over 200 languages<br>
    24/7/365
  </p>
</section>

<section class="card card--front" aria-label="Card front">
  <svg class="wave" width="700" height="400" viewBox="0 0 700 400" aria-hidden="true">
    <path d="M0,0 H700 V30 C560,120 280,70 0,120 Z" fill="var(--blue)"/>
    <path d="M0,120 C280,70 560,120 700,30 V40 C560,135 280,95 0,150 Z" fill="var(--white)"/>
    <path d="M0,150 C280,95 560,135 700,40 V46 C560,145 280,110 0,165 Z" fill="var(--blue)"/>
  </svg>

  <div class="brand">
    <span class="brand__mark"></span>
    <span class="brand__name">Corvana<br>Tongue<br>Works <small>LLC</small></span>
  </div>

  <div class="person">
    <p class="person__name">RHODA PELLING</p>
    <p class="person__title">President</p>
    <span class="person__bar"></span>
    <span class="person__accent"></span>
  </div>
  <div class="rule rule--name"></div>

  <p class="address">482 Garnet Ave., Ste. 219<br>Indianapolis, IN 40917 USA</p>

  <ul class="contacts">
    <li>
      <svg width="14" height="14" viewBox="0 0 24 24" aria-hidden="true"><path fill="var(--blue)" d="M6.6 10.8a15 15 0 0 0 6.6 6.6l2.2-2.2a1 1 0 0 1 1-.25 11.4 11.4 0 0 0 3.6.57 1 1 0 0 1 1 1V20a1 1 0 0 1-1 1A17 17 0 0 1 3 4a1 1 0 0 1 1-1h3.5a1 1 0 0 1 1 1c0 1.25.2 2.45.57 3.57a1 1 0 0 1-.25 1z"/></svg>
      (555) 481-3062
    </li>
    <li>
      <svg width="14" height="14" viewBox="0 0 24 24" aria-hidden="true"><rect x="2" y="5" width="20" height="14" rx="2" fill="none" stroke="var(--blue)" stroke-width="2.4"/><path d="M2 6l10 7 10-7" fill="none" stroke="var(--blue)" stroke-width="2.4"/></svg>
      rmpelling@corvanatongueworks.example
    </li>
    <li>
      <svg width="14" height="14" viewBox="0 0 24 24" aria-hidden="true"><circle cx="12" cy="12" r="10" fill="none" stroke="var(--blue)" stroke-width="2"/><ellipse cx="12" cy="12" rx="4.5" ry="10" fill="none" stroke="var(--blue)" stroke-width="2"/><path d="M2 12h20" stroke="var(--blue)" stroke-width="2"/></svg>
      www.corvanatongue.example
    </li>
  </ul>
</section>

</body>
</html>
```